Jolly Paws Business Card Update

I have a business card which I love. I want to keep the same logo, colours, font and style. I want to upgrade the scripting and remove some elements and add others.
On the front side under Services - remove the existing wording and insert - Providing individual coaching strategies to create happy, healthy and social canine companions
Under Denise Carvell amend the current wording to read: Qualified in Dog Behavioural Training, Natural Animal Healthcare and Animal Health Science
On the reverse side to remove the web address.

```html
<!DOCTYPE html>
<html lang="en">
<head>
<meta charset="utf-8">
<title>Jolly Paws Business Card</title>
<link rel="stylesheet" href="https://fonts.googleapis.com/css2?family=Open+Sans:wght@400;600;700&family=Arimo:wght@400;700&display=swap">
<style>
  :root {
    --bg: #2b2b2c;
    --blue-dark: #1f4f9e;
    --blue-mid: #1a6cc0;
    --blue-light: #0a8fd0;
    --red-dark: #6a1518;
    --red: #c81f24;
    --navy: #262a78;
    --paper: #f1f1f1;
    --cream: #efe7cf;
    --white: #ffffff;
  }
  html, body { margin: 0; padding: 0; }
  body {
    width: 1200px; height: 1138px; overflow: hidden;
    background: var(--bg);
    position: relative;
    font-family: "Open Sans", sans-serif;
  }
  .card {
    position: absolute; border-radius: 14px; overflow: hidden;
    box-shadow: 0 4px 10px rgba(0,0,0,.45);
  }

  /* Front */
  .card-front {
    left: 274px; top: 186px; width: 623px; height: 376px;
    background: linear-gradient(20deg, var(--blue-dark) 0%, var(--blue-mid) 50%, var(--blue-light) 100%);
  }
  .front-mark {
    position: absolute; left: 236px; top: 34px; width: 152px; height: 152px;
    border-radius: 50%; background: var(--cream); box-sizing: border-box;
    border: 10px solid var(--red);
  }
  .front-name {
    position: absolute; left: 0; right: 0; top: 192px; text-align: center;
    font-weight: 600; font-size: 40px; color: var(--white); letter-spacing: 1px; margin: 0;
  }
  .front-tagline {
    position: absolute; left: 0; right: 0; top: 236px; text-align: center;
    font-size: 20px; color: var(--white); margin: 0;
  }
  .front-band {
    position: absolute; left: 0; right: 0; top: 302px; bottom: 0;
    background: linear-gradient(90deg, var(--red-dark), var(--red) 55%, var(--red-dark));
  }
  .services-pill {
    position: absolute; left: 219px; top: 288px; width: 186px; height: 26px;
    border-radius: 13px; background: linear-gradient(#ffffff, #dfe3ea);
    border: 2px solid var(--blue-mid); box-sizing: border-box;
    text-align: center; font-weight: 700; font-size: 16px; line-height: 22px;
    letter-spacing: 2px; color: var(--navy);
  }
  .front-services {
    position: absolute; left: 0; right: 0; top: 319px; text-align: center;
    font-size: 16.5px; line-height: 22px; color: var(--white); margin: 0;
  }

  /* Back */
  .card-back {
    left: 275px; top: 607px; width: 619px; height: 376px;
    background: var(--paper);
  }
  .back-band {
    position: absolute; left: 230px; right: 0; top: 217px; height: 94px;
    background: linear-gradient(90deg, var(--red-dark), var(--red) 45%, var(--red-dark));
  }
  .back-shape { position: absolute; left: 0; top: 0; }
  .back-mark {
    position: absolute; left: 37px; top: 91px; width: 194px; height: 194px;
    border-radius: 50%; background: var(--cream); box-sizing: border-box;
    border: 14px solid var(--red);
  }
  .back-info {
    position: absolute; right: 28px; top: 32px; text-align: right; color: var(--navy);
  }
  .person-name { margin: 0; font-weight: 600; font-size: 26px; line-height: 34px; }
  .credentials { margin: 4px 0 0; font-size: 14.5px; line-height: 20px; }
  .contacts { list-style: none; margin: 8px 0 0; padding: 0; font-size: 15.5px; line-height: 22px; }
  .contacts li { display: flex; justify-content: flex-end; align-items: center; gap: 10px; }
  .contacts svg { width: 14px; height: 14px; }
  .back-services {
    position: absolute; right: 28px; top: 225px; text-align: right; color: var(--white);
    font-family: "Arimo", sans-serif; font-size: 16px; line-height: 19.5px;
  }
  .back-services h2 { margin: 0; font-size: 16px; font-weight: 700; }
  .back-services p { margin: 0; }
  .back-promise {
    position: absolute; right: 28px; top: 318px; text-align: right; color: var(--navy);
    font-family: "Arimo", sans-serif; font-size: 16px; line-height: 19.5px; margin: 0;
  }
</style>
</head>
<body>

<section class="card card-front">
  <div class="front-mark"></div>
  <h1 class="front-name">JOLLY PAWS</h1>
  <p class="front-tagline">HAPPY DOGS, HAPPY OWNERS</p>
  <div class="front-band"></div>
  <div class="services-pill">SERVICES</div>
  <p class="front-services">Providing individual coaching strategies to create happy,<br>healthy and social canine companions</p>
</section>

<section class="card card-back">
  <div class="back-band"></div>
  <svg class="back-shape" width="330" height="376" viewBox="0 0 330 376">
    <defs>
      <linearGradient id="backBlue" x1="0" y1="0" x2="0" y2="1">
        <stop offset="0" stop-color="#1a62b8"/>
        <stop offset="1" stop-color="#0f83cc"/>
      </linearGradient>
      <linearGradient id="backRed" x1="0" y1="0" x2="0" y2="1">
        <stop offset="0" stop-color="#c81f24"/>
        <stop offset="0.5" stop-color="#7a181b"/>
        <stop offset="1" stop-color="#c81f24"/>
      </linearGradient>
    </defs>
    <path d="M0 0 H238 Q318 188 224 376 H0 Z" fill="url(#backRed)"/>
    <path d="M0 0 H212 Q300 188 216 376 H0 Z" fill="url(#backBlue)"/>
  </svg>
  <div class="back-mark"></div>

  <div class="back-info">
    <h1 class="person-name">Denise Carvell</h1>
    <p class="credentials">Qualified in Dog Behavioural<br>Training, Natural Animal Healthcare<br>and Animal Health Science</p>
    <ul class="contacts">
      <li>0400 123 456
        <svg viewBox="0 0 14 14"><rect x="3" y="0.5" width="8" height="13" rx="1.5" fill="none" stroke="#c81f24" stroke-width="1.4"/><rect x="4.8" y="2.5" width="4.4" height="4" fill="#c81f24"/></svg>
      </li>
      <li>jollypaws1@mail.com
        <svg viewBox="0 0 14 14"><rect x="0.5" y="3" width="13" height="9" fill="#c81f24"/><path d="M0.5 3 L7 8 L13.5 3" fill="none" stroke="#fff" stroke-width="1"/></svg>
      </li>
    </ul>
  </div>

  <div class="back-services">
    <h2>SERVICES</h2>
    <p>Providing individual coaching<br>strategies to create happy, healthy<br>and social canine companions</p>
  </div>
  <p class="back-promise">Promoting communication and connection<br>between dogs &amp; their families</p>
</section>

</body>
</html>
```